Counseling Practice Business Card

I need a professional looking business card incorporating my new logo that was just completed. Card needs to incorporate my name and title, description of my specialty, my address, my phone number, my fax number, my email and my website URL. I need to be able to choose design on/with different paper colors and textures.
I do not have a lot of business card ideas so I am open to anything but I want bold,sharp, clear card without additional designs other than my logo (see attached file info). I am open to different color backgrounds or paper colors including black. I do not like traditional brackets around area codes in phone number or dashes between numbers in phone number. Am open to other ways of presenting including periods between numbers as appropriate. I do not know enough to know what I like yet but I want card to coordinate and work together with my logo. My practice emphasizes natural mental health interventions so any use of color (with background paper color or the blue and green in my logo) that elicits nature is nice. In addition to black, any natural brown or wood looking background might be desirable also. Most of the offerings so far look very similar and boring.

Target Market(s)

Potential therapy clients and other professionals

Contact Information for Business Card

Card information:
Gerald M. Whitcombe, Ph.D.
Licensed Clinical Psychologist
Integrative Health Coach
4812 Marlowe Ridge Blvd SE
Suite 310
Ashby Falls, GA 30412
(770) 415-2983 phone
(770) 581-4096 fax
drgeraldwhitcombe@quillmarsh.net
brightfernwellness.net

Font styles to use
Serif
Sans Serif
Other font styles liked:
• anything that you think looks crisp, clear and easily readable

Requirements
Must have
• Any color used should coordinate with my logo design (see attached files).
• Card should be printed horizontally so top and bottom are longest sides of rectangle.
• Background color or paper color should complement and highlight logo. Do not like a white background. black, grey, brown or any color my logo would blend well with.
Nice to have
• I would like designer to utilize color to highlight letters/name or phone-fax-web symbols.
• Bottom edge of card could be highlighted if appropriate to an idea.
Should not have
• I would NOT want the card to have a pure white background at all.
• No clear cards.
• Cards should be oriented with long sides on bottom and top, NOT sides. DO NOT LIKE THIS THIN TALL ORIENTATION.

```html
<!DOCTYPE html>
<html lang="en">
<head>
<meta charset="utf-8">
<title>Brightfern Wellness – Business Card</title>
<link rel="stylesheet" href="https://fonts.googleapis.com/css2?family=Roboto+Condensed:wght@400;700&family=Roboto:wght@400;500&display=swap">
<style>
  :root {
    --page: #e4e4e4;
    --card-dark: #1c1d1f;
    --brand-blue: #2f78c0;
    --brand-blue-text: #3a7fc4;
    --brand-green: #0f7a3c;
    --title-green: #1f8a45;
    --white: #ffffff;
    --silver: #c9c9c9;
  }
  * { margin: 0; padding: 0; box-sizing: border-box; }
  html, body {
    width: 1200px; height: 960px; overflow: hidden;
    background: var(--page);
    font-family: "Roboto", Arial, sans-serif;
  }
  .card {
    position: absolute; left: 314px; width: 600px; height: 342px;
    background: var(--card-dark); overflow: hidden;
  }
  .card--front { top: 126px; }
  .card--back { top: 531px; }
  .front-art { position: absolute; inset: 0; }
  .holder { position: absolute; left: 34px; top: 30px; }
  .holder__name {
    font-family: "Roboto Condensed", Arial, sans-serif; font-weight: 700;
    font-size: 20px; color: var(--brand-blue-text); text-transform: uppercase;
    line-height: 24px;
  }
  .holder__role {
    font-family: "Roboto Condensed", Arial, sans-serif; font-weight: 400;
    font-size: 15.5px; color: var(--title-green); line-height: 19px;
  }
  .practice-name {
    position: absolute; left: 28px; top: 136px;
    font-size: 31px; font-weight: 500; color: var(--brand-blue-text);
    white-space: nowrap;
  }
  .contact {
    position: absolute; right: 30px; top: 175px;
    text-align: right; color: var(--white); font-size: 14.5px; line-height: 19px;
  }
  .contact__address { margin-bottom: 9px; }
  .contact__line { display: flex; justify-content: flex-end; align-items: center; gap: 4px; }
  .contact__icon { width: 13px; height: 13px; fill: var(--white); flex: none; }
  .back-name {
    position: absolute; left: 0; right: 0; top: 142px; text-align: center;
    font-size: 46px; font-weight: 500; color: var(--silver); white-space: nowrap;
  }
</style>
</head>
<body>
  <section class="card card--front">
    <svg class="front-art" viewBox="0 0 600 342" width="600" height="342" aria-hidden="true">
      <rect width="600" height="342" fill="var(--brand-blue)"/>
      <path d="M0 0 L412 0 C432 20 436 90 405 160 C360 255 250 322 131 342 L0 342 Z" fill="var(--card-dark)"/>
      <path d="M296 17 C330 4 370 0 405 2 C428 25 428 95 398 165 C355 255 255 320 140 342 L131 342 C250 305 335 245 375 165 C405 100 395 40 296 17 Z" fill="var(--brand-green)"/>
    </svg>

    <div class="holder">
      <p class="holder__name">Gerald M. Whitcombe, Ph.D.</p>
      <p class="holder__role">Licensed Clinical Psychologist</p>
      <p class="holder__role">Integrative Health Coach</p>
    </div>

    <p class="practice-name">Brightfern Wellness</p>

    <div class="contact">
      <div class="contact__address">
        <p>4812 Marlowe Ridge Blvd SE</p>
        <p>Suite 310</p>
        <p>Ashby Falls, GA 30412</p>
      </div>
      <p class="contact__line">(770) 415-2983
        <svg class="contact__icon" viewBox="0 0 12 12" aria-label="phone"><path d="M2.5 0.5 L4.5 0.5 L5.3 3 L4 4.2 C4.7 5.7 6.3 7.3 7.8 8 L9 6.7 L11.5 7.5 L11.5 9.5 C11.5 10.6 10.6 11.5 9.5 11.5 C4.5 11.2 0.8 7.5 0.5 2.5 C0.5 1.4 1.4 0.5 2.5 0.5 Z"/></svg>
      </p>
      <p class="contact__line">(770) 581-4096
        <svg class="contact__icon" viewBox="0 0 12 12" aria-label="fax"><rect x="3" y="0.5" width="6" height="3"/><rect x="0.5" y="4" width="11" height="5" rx="1"/><rect x="3" y="8" width="6" height="3.5" fill="var(--white)" stroke="var(--brand-blue)" stroke-width="0.8"/></svg>
      </p>
      <p class="contact__line">drgeraldwhitcombe@quillmarsh.net
        <svg class="contact__icon" viewBox="0 0 12 12" aria-label="email"><path d="M0.5 2 L11.5 2 L11.5 10 L0.5 10 Z"/><path d="M0.5 2.3 L6 6.5 L11.5 2.3" fill="none" stroke="var(--brand-blue)" stroke-width="1"/></svg>
      </p>
      <p class="contact__line">www.brightfernwellness.net
        <svg class="contact__icon" viewBox="0 0 12 12" aria-label="website"><circle cx="6" cy="6" r="5.5"/><path d="M6 0.5 C3.5 3 3.5 9 6 11.5 M6 0.5 C8.5 3 8.5 9 6 11.5 M0.5 6 L11.5 6" fill="none" stroke="var(--brand-blue)" stroke-width="0.8"/></svg>
      </p>
    </div>
  </section>

  <section class="card card--back">
    <p class="back-name">Brightfern Wellness</p>
  </section>
</body>
</html>
```